PTV Website

We need a completely new modern design for our website www.ptv.org.au.

The Keyholders Alliance League of Australia Inc is a non-profit, volunteer-run association representing owners of strata-titled residential developments. We provide education, information and lobbying to improve the management of apartment complexes and the lives of those living in them. We’re all about “owners helping owners”. More information on our organisation can be seen at www.ptv.org.au.

Our new logo (from a recent PixelHarbor contest) is attached.

Target Market(s)

Primary audience - Owners of residential apartments - both resident owners and investor owners
Secondary audiences – current and potential sponsors; organisations providing products & services to Owners Corporations & Body Corporates

Industry/Entity Type

Non-Profit

Number of Pages Required

3 pages

Requirements
Must have
• We need:
- A design for the home page
- A design for 2-column content pages
- Fonts and colours for
* standard text
* H1, H2, H3 and H4 heading tags
* Bulleted and numbered lists
- A complementary colour scheme for the Calendar page
- A complementary breadcrumb format
- A standard format to display the associated tags for any content page

The above are described in more detail in the attached document.

The design should:
- be modern, uncluttered and clean
- reflect a sense of community, coupled with authority, professionalism and knowledge
- be a fixed width of 1000px

At a minimum the files we need are:
- The source file (PSD with all component layers is preferred, but not mandatory)
- JPG preview files
- Any stand-alone images as a PNG with transparent backgrounds
- Details of all fonts and sizes used (if they can’t be easily identified in the source files)

Note: The site is built with the Drupal CMS, so all page elements must be able to be clearly isolated.
Should not have
• Any fonts that are not freely available

```html
<!DOCTYPE html>
<html lang="en">
<head>
<meta charset="utf-8">
<title>PTV – Keyholders Alliance League of Australia</title>
<link rel="stylesheet" href="https://fonts.googleapis.com/css2?family=Arimo:wght@400;700&family=Noto+Sans:wght@400;700&display=swap">
<style>
:root{
  --blue:#1a46c4;
  --blue-deep:#0b34ad;
  --blue-text:#1d3f9d;
  --gold:#dba21f;
  --gold-dark:#b9830c;
  --page:#f4f4f4;
  --panel:#e9e9e9;
  --panel-line:#d4d4d4;
  --ink:#444;
  --ink-dark:#222;
  --sans:'Arimo',Arial,sans-serif;
  --small:'Noto Sans',Verdana,sans-serif;
}
*{box-sizing:border-box;margin:0;padding:0}
html,body{width:1200px;height:4162px;overflow:hidden;background:#fff}
body{position:relative;font-family:var(--sans);color:var(--ink)}
.page{position:absolute;left:14px;width:1172px;background:var(--page);box-shadow:0 0 6px rgba(0,0,0,.25);overflow:hidden}
.page-1{top:0;height:1373px}
.page-2{top:1437px;height:1309px}
.page-3{top:2786px;height:1316px}
.divider{position:absolute;left:0;width:1200px;height:3px;background:#222}
.abs{position:absolute}

/* header */
.brand{position:absolute;left:28px;top:20px;display:flex;align-items:flex-start;gap:26px}
.brand-mark{width:96px;height:96px;background:var(--gold);margin-top:6px}
.brand-name{font-family:var(--sans);font-size:31px;line-height:31px;letter-spacing:2px;color:var(--blue-text);padding-top:28px}
.search{position:absolute;left:737px;top:40px;width:412px;height:89px;background:linear-gradient(#fbfbfb,#eeeeee);border-radius:3px}
.search-input{position:absolute;left:11px;top:33px;width:280px;height:27px;background:#fff;border:1px solid #ddd}
.search-btn{position:absolute;left:304px;top:33px;width:88px;height:26px;background:var(--blue);color:#fff;font-size:19px;text-align:center;line-height:26px}
.nav{position:absolute;left:10px;top:158px;width:1155px;height:68px;background:linear-gradient(#e4aa2a,#cf9416 60%,#b98109);border-bottom:2px solid #a87408}
.nav span{position:absolute;top:19px;font-size:23px;color:#fff;text-shadow:0 1px 1px rgba(0,0,0,.35)}
.nav i{position:absolute;top:8px;width:1px;height:52px;background:rgba(255,255,255,.35)}
.rule{position:absolute;left:10px;top:232px;width:1155px;height:3px;background:var(--gold)}
.crumb{position:absolute;left:28px;top:246px;font-family:var(--small);font-size:12px;font-weight:700;color:var(--blue-text)}
.crumb b{display:inline-block;width:7px;height:7px;background:var(--gold);margin:0 3px 1px 10px}
.footer{position:absolute;left:10px;width:1155px;height:68px;background:linear-gradient(#dba21f,#c58c10);color:#fff;font-family:var(--small);font-size:13px;font-weight:700;text-align:center;line-height:68px;letter-spacing:.5px}
.page-1 .footer{top:1297px}
.page-2 .footer,.page-3 .footer{top:1227px}

/* home */
.hero{position:absolute;left:10px;top:231px;width:792px;height:205px;background:linear-gradient(90deg,var(--blue-deep),#1750d8);color:#fff;padding:48px 0 0 21px}
.hero p{font-size:23px;line-height:40px}
.hero strong{font-weight:400;font-size:33px}
.photo{position:absolute;left:806px;top:228px;width:362px;height:300px;background:linear-gradient(135deg,#9aa8c8,#5c6e98 55%,#2a3d70);border:5px solid #fff;box-shadow:2px 4px 10px rgba(0,0,0,.4);transform:rotate(3deg)}
.side-h{position:absolute;font-size:21px;font-weight:400;color:var(--blue-text)}
.box{position:absolute;background:var(--panel);border:2px solid var(--panel-line);padding:12px}
.login-label{font-family:var(--small);font-size:12px;font-weight:700;color:var(--ink-dark);margin-bottom:8px}
.login-input{width:215px;height:27px;background:#fff;border:1px solid #ddd;margin-bottom:18px}
.login-btn{width:92px;height:28px;background:var(--blue);color:#fff;font-size:17px;text-align:center;line-height:28px;margin-bottom:12px}
.login-link{font-family:var(--small);font-size:11px;font-weight:700;color:var(--ink-dark)}
.topics{list-style:none;font-family:var(--small);font-size:12px;font-weight:700;color:var(--ink-dark)}
.topics li{height:29px;display:flex;align-items:center;gap:10px}
.topics li::before{content:"";width:9px;height:9px;background:var(--blue)}
.vdots{position:absolute;width:0;border-left:2px dotted #bbb}
.main-h{position:absolute;font-size:27px;font-weight:400;color:var(--blue)}
.copy{font-size:14px;line-height:17px;color:var(--ink)}
.read-more{position:absolute;font-family:var(--small);font-size:12px;font-weight:700;color:var(--ink-dark);text-decoration:underline}
.news{position:absolute;left:317px;top:759px;width:544px;height:481px;background:linear-gradient(#f9f9f9,#e6e6e6);border:1px solid #ddd}
.news-title{position:absolute;left:14px;font-family:var(--small);font-size:14px;font-weight:700;color:var(--blue);text-decoration:underline}
.news-meta{position:absolute;left:14px;font-family:var(--small);font-size:11px;font-weight:700;color:var(--blue)}
.news .copy{position:absolute;left:14px;width:505px}
.more{position:absolute;left:14px;width:60px;height:22px;background:var(--gold);border:1px solid #a87408;font-family:var(--small);font-size:11px;font-weight:700;color:#222;text-align:center;line-height:20px}
.panel-text{font-size:12.5px;line-height:15px;color:#333}
.panel-text p{margin-bottom:15px}

/* content page */
.articles{position:absolute;left:26px;top:354px;list-style:none;font-family:var(--small);font-size:12.5px;line-height:16px;font-weight:700;color:var(--blue-text);width:330px}
.articles li{display:flex;gap:14px;margin-bottom:16px}
.articles li::before{content:"";flex:none;width:8px;height:8px;background:var(--gold);margin-top:4px}
.article{position:absolute;left:390px;width:760px}
.article h2{font-size:19px;font-weight:400;color:var(--blue-text);letter-spacing:.6px;margin-bottom:14px}
.article p{font-size:14px;line-height:17px;color:#444;margin-bottom:17px}

/* calendar */
.views{position:absolute;top:327px;font-family:var(--small);font-size:13px;font-weight:700;color:var(--blue-text)}
.cal{position:absolute;left:26px;top:350px;width:1100px}
.cal-bar{height:42px;background:linear-gradient(#2a5ede,#173fb8);color:#fff;font-family:var(--small);font-size:13px;font-weight:700;display:flex;justify-content:space-between;align-items:center;padding:0 14px;border:1px solid #0f2e8e}
.cal-grid{display:grid;grid-template-columns:25px 134px 143px 143px 177px 163px 134px 181px;margin-top:4px}
.cal-head{height:32px;background:linear-gradient(#d9a022,#b88009);color:#fff;font-family:var(--small);font-size:12px;font-weight:700;text-align:center;line-height:32px;border-right:1px solid #c89830}
.cal-cell{position:relative;background:#e5e5e5;border-right:1px solid #f4f4f4;border-bottom:1px solid #f4f4f4}
.cal-cell.lead{background:#dedede}
.day{position:absolute;right:0;top:0;min-width:30px;height:20px;background:#3d6ee0;color:#fff;font-family:var(--small);font-size:12px;font-weight:700;text-align:center;line-height:20px;padding:0 4px}
.popup{position:absolute;left:491px;top:837px;width:325px;height:225px;background:#1656e8;border:3px solid #fff;outline:1px solid #0d3bb0;color:#fff;font-family:var(--small);font-size:12.5px;line-height:15px;font-weight:700;padding:10px 12px}
.popup .close{position:absolute;right:8px;top:6px;font-size:17px}
.badge{position:absolute;right:8px;top:36px;width:88px;height:74px;background:#fff}
</style>
</head>
<body>

<!-- PAGE 1 : HOME -->
<section class="page page-1">
  <div class="brand"><div class="brand-mark"></div><div class="brand-name">KEYHOLDERS<br>ALLIANCE<br>LEAGUE</div></div>
  <div class="search"><div class="search-input"></div><div class="search-btn">Search</div></div>
  <nav class="nav">
    <span style="left:28px">Home</span><i style="left:111px"></i>
    <span style="left:123px">About</span><i style="left:204px"></i>
    <span style="left:220px">News</span><i style="left:298px"></i>
    <span style="left:314px">Events</span><i style="left:404px"></i>
    <span style="left:420px">Membership</span><i style="left:569px"></i>
    <span style="left:585px">Sponsorship</span><i style="left:729px"></i>
    <span style="left:745px">Links</span><i style="left:819px"></i>
    <span style="left:835px">Contact</span><i style="left:935px"></i>
    <span style="left:951px">Members Only</span>
  </nav>
  <div class="hero">
    <p><strong>Owners</strong> Helping Owners</p>
    <p><strong>Representing</strong> Strata Title Residential Developments</p>
    <p><strong>Lobbying and Sharing</strong> Information to Improve Apartment Living</p>
  </div>
  <div class="photo" role="img" aria-label="Photo of residents talking on an apartment balcony"></div>

  <h3 class="side-h" style="left:23px;top:498px">Member Login</h3>
  <div class="box" style="left:23px;top:533px;width:262px;height:210px;padding:14px 16px">
    <div class="login-label">Username or e-mail: *</div>
    <div class="login-input"></div>
    <div class="login-label">Password: *</div>
    <div class="login-input"></div>
    <div class="login-btn">LOGIN</div>
    <div class="login-link">Request new password</div>
  </div>

  <h3 class="side-h" style="left:23px;top:778px">Topic List</h3>
  <div class="box" style="left:23px;top:811px;width:262px;height:190px;padding:10px 14px">
    <ul class="topics">
      <li>Lorem ipsum.</li><li>Dolor sit amet, consectetur.</li><li>Adipisicing elit, sed do.</li>
      <li>Eiusmod tempor incididunt ut et.</li><li>Dolore magna aliqua.</li><li>Ut enim ad veniam, nostrud.</li>
    </ul>
  </div>

  <div class="vdots" style="left:301px;top:500px;height:776px"></div>
  <h2 class="main-h" style="left:317px;top:502px">Featured Announcements</h2>
  <p class="copy abs" style="left:317px;top:545px;width:525px">What happens when complaints get trampled underfoot. When is a bylaw not a bylaw? When the Residential Strata Review Panel decides it doesn't really matter.</p>
  <p class="copy abs" style="left:317px;top:612px;width:525px">Government reintroduce clamping and towing of illegally parked cars to stop protracted legal and sometimes physical disputes they say are turning apartment car parks into battle grounds</p>
  <span class="read-more" style="left:738px;top:685px">Read More...</span>

  <h2 class="main-h" style="left:317px;top:714px">Recent News</h2>
  <div class="news">
    <span class="news-title" style="top:32px">Bye bye to bylaws</span>
    <span class="news-meta" style="top:67px">Submitted by admin on 9 December 2009</span>
    <p class="copy" style="top:100px">What happens when complaints get trampled underfoot. When is a bylaw not a bylaw? When the Residential Strata Review Panel decides it doesn't really matter, that's when</p>
    <div class="more" style="top:167px">More...</div>
    <span class="news-title" style="top:253px">Push to clamp illegal parkers</span>
    <span class="news-meta" style="top:288px">Submitted by admin on 9 December 2009</span>
    <p class="copy" style="top:322px">RESIDENTS in flats and other strata buildings are demanding the State Government reintroduce clamping and towing of illegally parked cars to stop protracted legal and sometimes physical disputes they say are turning apartment car parks into battle grounds</p>
    <div class="more" style="top:424px">More...</div>
  </div>

  <div class="vdots" style="left:873px;top:500px;height:776px"></div>
  <h3 class="side-h" style="left:887px;top:537px">Upcoming Events</h3>
  <div class="box panel-text" style="left:887px;top:569px;width:262px;height:185px;padding:20px 10px">
    <p>Lorem ipsum dolor sit amet, ceius-mod tempor incididunt ut labore et.</p>
    <p>Dolore magna aliqua. Ut enim ad minim veniam, quis nostrud.</p>
    <p>ExDuis aute irure dolor in repre-henderit in voluptate.</p>
  </div>
  <h3 class="side-h" style="left:887px;top:786px">Recent Forum Posts</h3>
  <div class="box panel-text" style="left:887px;top:819px;width:262px;height:186px;padding:16px 10px">
    <p>Lorem ipsum dolor sit amet, consectetur adipisicincididunt ut labore et.</p>
    <p>Dolore magna aliqua. Ut enim ad minim veniam, quis nostrud.</p>
    <p>Exercitation ullamcoe dolor in reprehenderit in voluptate.</p>
  </div>

  <footer class="footer">©Keyholders Alliance League Inc 2008 | Disclaimer | Contact Us</footer>
</section>

<div class="divider" style="top:1436px"></div>

<!-- PAGE 2 : CONTENT -->
<section class="page page-2">
  <div class="brand"><div class="brand-mark"></div><div class="brand-name">KEYHOLDERS<br>ALLIANCE<br>LEAGUE</div></div>
  <div class="search"><div class="search-input"></div><div class="search-btn">Search</div></div>
  <nav class="nav">
    <span style="left:28px">Home</span><i style="left:111px"></i>
    <span style="left:123px">About</span><i style="left:204px"></i>
    <span style="left:220px">News</span><i style="left:298px"></i>
    <span style="left:314px">Events</span><i style="left:404px"></i>
    <span style="left:420px">Membership</span><i style="left:569px"></i>
    <span style="left:585px">Sponsorship</span><i style="left:729px"></i>
    <span style="left:745px">Links</span><i style="left:819px"></i>
    <span style="left:835px">Contact</span><i style="left:935px"></i>
    <span style="left:951px">Members Only</span>
  </nav>
  <div class="rule"></div>
  <div class="crumb">Home<b></b>Members Area</div>

  <h3 class="side-h" style="left:26px;top:300px;font-size:19px">Articles</h3>
  <ul class="articles">
    <li>Building Managements Rights-<br>Buyers Beware</li>
    <li>Building Owners &amp; Occupiers-<br>How Up to date must they be (AS 1851)</li>
    <li>Deffects</li>
    <li>Demistifying High-Rise Fire Safety</li>
    <li>Executive Committees</li>
    <li>Fire Safety and the new standrds<br>( AS 1851-2005 )</li>
    <li>Insurance Tips For Stats Plan</li>
    <li>Noise</li>
    <li>Owners Corporation &amp; GST</li>
    <li>Serviced Appartments- A New Fom<br>Of Starta Abuse</li>
    <li>Smoke Alarms</li>
    <li>Strata Managers</li>
    <li>Which Way to Vote?<br>The Burden of Choice!</li>
  </ul>
  <h3 class="side-h" style="left:26px;top:847px;font-size:17px">Topic List</h3>
  <div class="box" style="left:26px;top:877px;width:264px;height:189px;padding:10px 14px">
    <ul class="topics">
      <li>Lorem ipsum.</li><li>Dolor sit amet, consectetur.</li><li>Adipisicing elit, sed do.</li>
      <li>Eiusmod tempor incididunt ut et.</li><li>Dolore magna aliqua.</li><li>Ut enim ad veniam, nostrud.</li>
    </ul>
  </div>

  <div class="vdots" style="left:367px;top:299px;height:880px"></div>

  <article class="article" style="top:300px">
    <h2>Building Managements Rights- Buyers Beware</h2>
    <p>The Keyholders Alliance League of Australia (PTV) is the peak body representing apartment owners, with most members drawn from Owners Corporations' Executive Committees (ECs) or con-cerned apartment owners around Australia. PTV is a not-for-profit association.</p>
    <p>Through representation, lobbying, information-sharing and networking, we perform a vital service for our members that supports them in living in and/or investing in strata titled property.</p>
    <p>We lobby for changes necessary to Government policy and legislation, and sit on many Government and industry boards and panels to present our views to those in power. The PTV gives members a voice at both State and Federal levels, and an opportunity to put forward their views on problems, solutions and the kind of future that, as apartment owners, we'd all like to see.</p>
  </article>
  <article class="article" style="top:579px">
    <h2>Building Owners &amp; Occupiers- How Up to date must they be (AS 1851)</h2>
    <p>The PTV educates EC members and individuals by sharing experiences and disseminating informa-tion from relevant sources and related organisations.</p>
    <p>Regular meetings, seminars and an online discussion group give members access to fellow members' experiences in areas such as defects rectification, strata disputes, shared services, and levy management. These resources may save members thousands of dollars and an immense amount of heartache in the long run!</p>
  </article>
  <article class="article" style="top:791px">
    <h2>Deffects</h2>
    <p>Regular meetings, seminars and an online discussion group give members access to fellow members' experiences in areas such as defects rectification, strata disputes, shared services, and levy management. These resources may save members thousands of dollars and an immense amount of heartache in the long run!</p>
  </article>
  <article class="article" style="top:940px">
    <h2>Demistifying High-Rise Fire Safety</h2>
    <p>Regular meetings, seminars and an online discussion group give members access to fellow members' experiences in areas such as defects rectification, strata disputes, shared services, and levy management. These resources may save members thousands of dollars and an immense amount of heartache in the long run!</p>
  </article>

  <footer class="footer">©Keyholders Alliance League Inc 2008 | Disclaimer | Contact Us</footer>
</section>

<div class="divider" style="top:2750px"></div>
<div class="divider" style="top:2784px"></div>

<!-- PAGE 3 : CALENDAR -->
<section class="page page-3">
  <div class="brand"><div class="brand-mark"></div><div class="brand-name">KEYHOLDERS<br>ALLIANCE<br>LEAGUE</div></div>
  <div class="search"><div class="search-input"></div><div class="search-btn">Search</div></div>
  <nav class="nav">
    <span style="left:28px">Home</span><i style="left:111px"></i>
    <span style="left:123px">About</span><i style="left:204px"></i>
    <span style="left:220px">News</span><i style="left:298px"></i>
    <span style="left:314px">Events</span><i style="left:404px"></i>
    <span style="left:420px">Membership</span><i style="left:569px"></i>
    <span style="left:585px">Sponsorship</span><i style="left:729px"></i>
    <span style="left:745px">Links</span><i style="left:819px"></i>
    <span style="left:835px">Contact</span><i style="left:935px"></i>
    <span style="left:951px">Members Only</span>
  </nav>
  <div class="rule"></div>
  <div class="crumb">Home<b></b>Events</div>

  <h3 class="side-h" style="left:25px;top:308px;font-size:19px">Events</h3>
  <span class="views" style="left:895px">Year</span>
  <span class="views" style="left:955px">Month</span>
  <span class="views" style="left:1026px">Week</span>
  <span class="views" style="left:1094px">Day</span>

  <div class="cal">
    <div class="cal-bar"><span>« Prev</span><span>January 2010</span><span>Next »</span></div>
    <div class="cal-grid">
      <div class="cal-head"></div><div class="cal-head">Sunday</div><div class="cal-head">Monday</div><div class="cal-head">Tuesday</div><div class="cal-head">Wednesday</div><div class="cal-head">Thursday</div><div class="cal-head">Friday</div><div class="cal-head">Saturday</div>

      <div class="cal-cell lead" style="height:86px"></div><div class="cal-cell"></div><div class="cal-cell"></div><div class="cal-cell"></div><div class="cal-cell"></div><div class="cal-cell"></div><div class="cal-cell"><span class="day">1</span></div><div class="cal-cell"><span class="day">2</span></div>

      <div class="cal-cell lead" style="height:100px"></div><div class="cal-cell"><span class="day">3</span></div><div class="cal-cell"><span class="day">4</span></div><div class="cal-cell"><span class="day">5</span></div><div class="cal-cell"><span class="day">6</span></div><div class="cal-cell"><span class="day">7</span></div><div class="cal-cell"><span class="day">8</span></div><div class="cal-cell"><span class="day">9</span></div>

      <div class="cal-cell lead" style="height:90px"></div><div class="cal-cell"><span class="day">10</span></div><div class="cal-cell"><span class="day">11</span></div><div class="cal-cell"><span class="day">12</span></div><div class="cal-cell"><span class="day">13</span></div><div class="cal-cell"><span class="day">14</span></div><div class="cal-cell"><span class="day">15</span></div><div class="cal-cell"><span class="day">16</span></div>

      <div class="cal-cell lead" style="height:95px"></div><div class="cal-cell"><span class="day">17</span></div><div class="cal-cell"><span class="day">18</span></div><div class="cal-cell"><span class="day">19</span></div><div class="cal-cell"><span class="day">20</span></div><div class="cal-cell"><span class="day">21</span></div><div class="cal-cell"><span class="day">22</span></div><div class="cal-cell"><span class="day">23</span></div>

      <div class="cal-cell lead" style="height:97px"></div><div class="cal-cell"><span class="day">24</span></div><div class="cal-cell"><span class="day">25</span></div><div class="cal-cell"><span class="day">26</span></div><div class="cal-cell"><span class="day">27</span></div><div class="cal-cell"><span class="day">28</span></div><div class="cal-cell"><span class="day">29</span></div><div class="cal-cell"><span class="day">30</span></div>

      <div class="cal-cell lead" style="height:100px"></div><div class="cal-cell"><span class="day">31</span></div><div class="cal-cell"></div><div class="cal-cell"></div><div class="cal-cell"></div><div class="cal-cell"></div><div class="cal-cell"></div><div class="cal-cell"></div>
    </div>
  </div>

  <div class="popup">
    <div>SRMI Consumer Awareness Seminar</div>
    <span class="close">✕</span>
    <div class="badge"></div>
    <div style="margin-top:16px">Time: 24 February 2010<br>6:15pm - 7:45pm</div>
    <div style="margin-top:16px">Location:<br>Harbourview Conference Centre<br>148 Ferris Street</div>
    <div style="margin-top:16px">Sydney<br>Organiser: Strata Registry<br>Management Institute</div>
  </div>

  <footer class="footer">©Keyholders Alliance League Inc 2008 | Disclaimer | Contact Us</footer>
</section>

<div class="divider" style="top:4108px"></div>
</body>
</html>
```